New Business Card Design for Manufacturing

We are an engineering/manufacturing company that offers Advanced machining/assembly/engineering services, as well as innovative products for the heavy duty engine cooling markets.

We are looking to get a new business card designed that is clean and modern looking, but still fits the wide range of technical/skilled work we do.

- We hope to use this design as the base for other design work in new Presentations, web, and print work.

Industry/Entity Type

Engineering

Contact Information for Business Card

Our preferred color of blue is (RGB) 22/71/159 but can vary slightly from that color. Our content will be our Logo and full company name (Vantrell Forge Works, Inc.), company address, name, job title, phone number with extension, cell number, fax number, website, and email address on the cards.
We'd like the full company name next to the logo, but we are open to other interpretations of that layout.
Preferably, we would like the back side to be clean with just our logo, and the front to contain all of the contact information.

Colors
2f74b4
0355a3
85abd2

Requirements
Must have
• - Logo, company name, needed content - We are open to interpretation beyond that.
• - Standard size business card.
• - Horizontal orientation.
• - Enough space for lengthy names / job titles (for example, a job title could read "Directory of Human Resources" or "V.P. of Governmental Affairs"). We need this to look clean, whether the title be short (CEO) or long (as described above).

```html
<!DOCTYPE html>
<html lang="en">
<head>
<meta charset="utf-8">
<title>Vantrell Forge Works – Business Card</title>
<link rel="stylesheet" href="https://fonts.googleapis.com/css2?family=Open+Sans:wght@400;600&family=Roboto:wght@700;900&display=swap">
<style>
  :root {
    --brand-blue: #0f4fa0;
    --card-light: #f2f3f5;
    --notch-grey: #8a8f96;
    --text-white: #ffffff;
    --page-bg: #e4e6ea;
  }
  html, body {
    margin: 0;
    width: 1200px;
    height: 900px;
    overflow: hidden;
    background: var(--page-bg);
  }
  .business-card {
    position: absolute;
    left: 177px;
    top: 188px;
    width: 846px;
    height: 524px;
    display: flex;
    box-shadow: 0 10px 30px rgba(0,0,0,0.15);
  }
  .contact-panel {
    position: relative;
    width: 413px;
    background: var(--brand-blue);
    color: var(--text-white);
    text-align: right;
    box-sizing: border-box;
    padding: 58px 52px 0 20px;
    font-family: "Open Sans", Arial, sans-serif;
  }
  .contact-panel::after {
    content: "";
    position: absolute;
    right: -1px;
    top: 70px;
    border-top: 20px solid transparent;
    border-bottom: 20px solid transparent;
    border-right: 28px solid var(--notch-grey);
  }
  .person-name {
    margin: 0;
    font-family: "Roboto", Arial, sans-serif;
    font-weight: 700;
    font-size: 31px;
    line-height: 1.1;
    letter-spacing: 0.3px;
  }
  .job-title {
    margin: 2px 0 0;
    font-size: 21px;
    line-height: 1.2;
  }
  .contact-list {
    list-style: none;
    margin: 92px 0 0;
    padding: 0;
    font-size: 21px;
    line-height: 31px;
  }
  .contact-list li {
    display: flex;
    justify-content: flex-end;
    align-items: center;
    gap: 6px;
    margin-right: -22px;
  }
  .contact-icon {
    width: 16px;
    height: 16px;
    fill: var(--text-white);
    flex: none;
  }
  .postal-address {
    margin: 16px 0 0;
    font-style: normal;
    font-size: 21px;
    line-height: 31px;
  }
  .brand-panel {
    flex: 1;
    background: var(--card-light);
    display: flex;
    align-items: center;
    justify-content: center;
  }
  .brand-lockup {
    display: flex;
    align-items: center;
    gap: 14px;
    margin-top: -30px;
  }
  .brand-square {
    width: 46px;
    height: 46px;
    background: var(--brand-blue);
  }
  .brand-name {
    font-family: "Roboto", Arial, sans-serif;
    font-weight: 900;
    font-size: 34px;
    line-height: 1.05;
    color: var(--brand-blue);
    text-transform: uppercase;
  }
</style>
</head>
<body>
  <div class="business-card">
    <section class="contact-panel">
      <h1 class="person-name">DANIEL HARROW</h1>
      <p class="job-title">Managing Director</p>
      <ul class="contact-list">
        <li>(044)123456789
          <svg class="contact-icon" viewBox="0 0 16 16"><path d="M1 6c0-2 3-3 7-3s7 1 7 3v1h-3V5.5H4V7H1zM3 8h10l1 6H2z"/></svg></li>
        <li>(044)123456789
          <svg class="contact-icon" viewBox="0 0 16 16"><path d="M4 1h8v14H4zM5.5 3v9h5V3z"/></svg></li>
        <li>(044)123456789
          <svg class="contact-icon" viewBox="0 0 16 16"><path d="M2 5h12v10H2zM4 1h7v4H4zM4 8h3v2H4zm5 0h3v2H9zM4 11h3v2H4zm5 0h3v2H9z"/></svg></li>
        <li>info@youremail.com
          <svg class="contact-icon" viewBox="0 0 16 16"><path d="M1 3h14v10H1zM2.5 4.5 8 9l5.5-4.5z"/></svg></li>
        <li>www.websitename.com
          <svg class="contact-icon" viewBox="0 0 16 16"><circle cx="8" cy="8" r="7"/></svg></li>
      </ul>
      <address class="postal-address">1234, Address GoesHere<br>Country name, 12345</address>
    </section>
    <section class="brand-panel">
      <div class="brand-lockup">
        <div class="brand-square"></div>
        <div class="brand-name">Vantrell<br>Forge Works</div>
      </div>
    </section>
  </div>
</body>
</html>
```